Moxy Fen needs some awesome stationary

Do you have what it takes to get my brand? You either do or you don't, have a crack at a design and you my just win my business.

I don't want to waste your or my time, so put your creative genius on either a business card or envelope.

I however need a package of stationary that follows the same brand. I will message you to complete the remaining should I like your first submission.

Here is what I need, have a go!

Basically I need the following for my small business based in melbourne.
- Letterhead (printer ready and MS Word)
- Business Card
- Compliments Slip
- Envelope
- Proposal Cover Page (MS Word only)
- Presentation Folder
- Marbled Fox Cards
- Student Name Tent
- Index Cards
- Vell-Ka

I am establishing the brand and it must be modern, professional but also relaxed; that is not formal and not corporate. It represents a company are leaders, but small enough to care and operate like a bunch of friends. We are bringing people and conversations back to business, and turfing out all the bureaucracy and crazy and wasteful procedures. Its about "lets talk and figure it out together and find even better ways".

Target Market(s)

Mainly companies that build software products, but Agile practices are used in many other industries (even graphic design projects)

Industry/Entity Type

Information Technology

Font styles to use
Sans Serif

Colors
3176b5
aaaaaa

Requirements
Must have
• I like curves and circles and not boxes or rectangles.
• I want a colour rich design with my brand colours, but it must be balanced.
• I want more modern than traditional, but simple modern
Should not have
• Not corporate
• Please don't waste my time if your not going to think about it.
• Don't mess with my primary logo
• Don't change my colours
• Don't overlay logo on image

```html
<!DOCTYPE html>
<html lang="en">
<head>
<meta charset="utf-8">
<title>Moxy Fen – Index Cards and Name Tents</title>
<link rel="stylesheet" href="https://fonts.googleapis.com/css2?family=Open+Sans:wght@400;600;700&display=swap">
<style>
  :root {
    --canvas: #898a8e;
    --brand-blue: #2c5ba4;
    --brand-coral: #ff8080;
    --brand-grey: #a9adb8;
    --fold-grey: #d0d0d0;
    --paper: #ffffff;
    --rule: #555a63;
    --ink-soft: #4a4a4a;
    --stamp-ring: #bdbdbd;
  }
  * { margin: 0; padding: 0; box-sizing: border-box; }
  html, body { width: 1190px; height: 1200px; overflow: hidden; }
  body {
    background: var(--canvas);
    font-family: "Open Sans", Arial, sans-serif;
    position: relative;
  }

  /* Index cards */
  .index-card {
    position: absolute;
    top: 99px;
    width: 456px;
    height: 542px;
    background: var(--paper);
    box-shadow: 0 1px 4px rgba(0,0,0,0.35);
  }
  .index-card--blue { left: 120px; }
  .index-card--coral { left: 632px; }
  .index-card__header { height: 75px; }
  .index-card--blue .index-card__header { background: var(--brand-blue); }
  .index-card--coral .index-card__header { background: var(--brand-coral); }

  .index-card__rule {
    position: absolute;
    left: 35px;
    width: 389px;
    border-top: 1px dotted var(--rule);
  }

  .index-card__brand {
    position: absolute;
    left: 29px;
    top: 497px;
    display: flex;
    align-items: center;
    gap: 6px;
  }
  .brand-dot {
    width: 20px; height: 20px;
    border-radius: 50%;
    background: var(--brand-blue);
  }
  .brand-name {
    font-weight: 700;
    font-size: 18px;
    color: var(--brand-blue);
    line-height: 1;
  }
  .index-card__tagline {
    position: absolute;
    left: 201px;
    top: 502px;
    font-size: 12.5px;
    color: var(--ink-soft);
  }
  .index-card__stamp {
    position: absolute;
    left: 359px;
    top: 462px;
    width: 65px; height: 65px;
    border-radius: 50%;
    border: 1px solid var(--stamp-ring);
  }

  /* Name tents */
  .name-tent {
    position: absolute;
    left: 195px;
    width: 739px;
    height: 135px;
  }
  .name-tent--swoop { top: 756px; }
  .name-tent--panel { top: 955px; }
  .tent-name {
    font-family: "Open Sans", Arial, sans-serif;
    font-weight: 600;
    font-size: 56px;
    fill: var(--brand-blue);
  }
  .tent-brand {
    font-family: "Open Sans", Arial, sans-serif;
    font-weight: 700;
    font-size: 13px;
  }
</style>
</head>
<body>

  <section class="index-card index-card--blue">
    <div class="index-card__header"></div>
    <div class="index-card__rule" style="top:119px"></div>
    <div class="index-card__rule" style="top:181px"></div>
    <div class="index-card__rule" style="top:244px"></div>
    <div class="index-card__rule" style="top:306px"></div>
    <div class="index-card__rule" style="top:370px"></div>
    <div class="index-card__rule" style="top:431px"></div>
    <div class="index-card__brand"><span class="brand-dot"></span><span class="brand-name">Moxy Fen</span></div>
    <div class="index-card__tagline">Get It Done</div>
    <div class="index-card__stamp"></div>
  </section>

  <section class="index-card index-card--coral">
    <div class="index-card__header"></div>
    <div class="index-card__rule" style="top:119px"></div>
    <div class="index-card__rule" style="top:181px"></div>
    <div class="index-card__rule" style="top:244px"></div>
    <div class="index-card__rule" style="top:306px"></div>
    <div class="index-card__rule" style="top:370px"></div>
    <div class="index-card__rule" style="top:431px"></div>
    <div class="index-card__brand"><span class="brand-dot"></span><span class="brand-name">Moxy Fen</span></div>
    <div class="index-card__tagline">Get It Done</div>
    <div class="index-card__stamp"></div>
  </section>

  <svg class="name-tent name-tent--swoop" viewBox="0 0 591 108" aria-label="Name tent, swoop edge">
    <polygon points="0,88 25,0 31,0 31,88" fill="var(--fold-grey)"/>
    <rect x="31" y="0" width="560" height="108" fill="var(--brand-blue)"/>
    <path d="M548,0 C588,14 586,82 512,108 H498 C578,72 576,12 548,0 Z" fill="var(--brand-grey)"/>
    <path d="M31,0 H548 C576,12 578,72 498,108 H31 Z" fill="var(--paper)"/>
    <text class="tent-name" x="59" y="78">ELLA MARSH</text>
    <circle cx="487" cy="38" r="15" fill="var(--brand-blue)"/>
    <text class="tent-brand" x="487" y="80" text-anchor="middle" fill="var(--brand-blue)">Moxy Fen</text>
  </svg>

  <svg class="name-tent name-tent--panel" viewBox="0 0 591 108" aria-label="Name tent, panel edge">
    <polygon points="0,88 25,0 31,0 31,88" fill="var(--fold-grey)"/>
    <rect x="31" y="0" width="560" height="108" fill="var(--brand-blue)"/>
    <path d="M459,0 C490,26 488,78 452,108 H432 C486,78 486,24 459,0 Z" fill="var(--brand-grey)"/>
    <path d="M31,0 H459 C482,24 482,76 432,108 H31 Z" fill="var(--paper)"/>
    <text class="tent-name" x="59" y="78">ELLA MARSH</text>
    <circle cx="532" cy="42" r="15" fill="var(--paper)"/>
    <text class="tent-brand" x="532" y="80" text-anchor="middle" fill="var(--paper)">Moxy Fen</text>
  </svg>

</body>
</html>
```